Candle Rental Business seeks new website design

We need a new website design for a Candle hire business. The business rents out pillar candles for events such as weddings and corporate events. Our main target market is weddings. The business name is Hire a Lantern. The business name does not have a logo design.

We would like a website that is light in colours and creates a warm atmosphere. The design needs to be elegant and upmarket. There are different size candles that we hire out, ranging from 10cm diameter to 20cm diameter, flat, tall etc. All our candles are white in colour. Its just the size that differs.

We would also like to include a section for hiring out decor such as glassvases, candlebras, overlays and chairs sachets, chair covers. However, this is not the businesses main focus but an additional offering to customers.

Target Market(s)

Wedding venues and brides. Corporate events. School dances.

Industry/Entity Type

Hospitality

Logo Text

Hire a Lantern

Number of Pages Required

1 page

Font styles to use
Sans Serif
Script

Requirements
Must have
• Pictures of pillar candles. Plain white candles. The website must centre around candles.
Nice to have
• Different examples of candle centrepieces
Should not have
• Pictures must not be of brides. Pictures of surrounding is perferable.

```html
<!DOCTYPE html>
<html lang="en">
<head>
<meta charset="utf-8">
<title>Hire a Lantern – Candle Hire</title>
<link href="https://fonts.googleapis.com/css2?family=Questrial&family=Lato:wght@400;700&family=Poppins:wght@600&display=swap" rel="stylesheet">
<style>
:root{
  --orange:#f07a14;
  --amber:#fdb913;
  --ink:#222222;
  --text:#555555;
  --muted:#777777;
  --slate:#5f6062;
  --grey-band:#ececec;
  --cream-band:#f5f2e6;
  --footer:#efefef;
  --bar:#303030;
  --white:#ffffff;
  --link-blue:#3a8fd6;
}
*{box-sizing:border-box;margin:0;padding:0}
html,body{width:1200px;height:2757px;overflow:hidden;background:var(--white)}
body{position:relative;font-family:"Lato",sans-serif;color:var(--text)}
.heading{font-family:"Questrial",sans-serif;color:var(--ink);font-weight:400;font-size:41px;text-align:center;width:100%}

/* header */
.site-header{position:absolute;left:0;top:0;width:1200px;height:120px;background:var(--white)}
.brand{position:absolute;left:81px;top:38px;display:flex;align-items:center;gap:16px}
.brand-mark{width:24px;height:24px;background:var(--orange)}
.brand-name{font-family:"Questrial",sans-serif;font-size:42px;color:var(--ink);line-height:1}
.account{position:absolute;top:24px;right:82px;display:flex;gap:34px;font-size:14px;color:var(--muted)}
.account span{display:flex;align-items:center;gap:8px}
.main-nav{position:absolute;top:68px;right:82px;display:flex;gap:40px;font-family:"Questrial",sans-serif;font-size:16px;color:var(--ink)}
.main-nav a{color:inherit;text-decoration:none;padding:4px 8px}
.main-nav a.active{color:var(--orange);border:1px solid var(--orange)}

/* hero */
.hero{position:absolute;left:0;top:120px;width:1200px;height:532px;
  background:radial-gradient(ellipse at 50% 45%,#f6e6b4 0%,#c9b79a 22%,#8b7f79 48%,#5a4f52 100%)}
.hero-arrow{position:absolute;top:230px}
.hero-caption{position:absolute;left:0;bottom:0;width:100%;height:51px;background:rgba(30,26,26,.72);
  color:var(--white);font-family:"Poppins",sans-serif;font-weight:600;font-size:29px;text-align:center;line-height:51px;letter-spacing:.6px;text-transform:uppercase}

/* about */
.about{position:absolute;left:0;top:652px;width:1200px;height:296px}
.about .heading{position:absolute;top:48px}
.about p{position:absolute;left:84px;top:110px;width:1032px;text-align:center;font-size:14px;line-height:26px;color:var(--text)}
.btn{display:inline-block;font-size:15px;text-align:center;color:var(--white)}
.btn-orange{background:var(--orange)}
.read-more{position:absolute;left:542px;top:207px;width:116px;height:37px;line-height:37px}

/* products */
.products{position:absolute;left:0;top:948px;width:1200px;height:627px;background:var(--grey-band)}
.products .heading{position:absolute;top:52px}
.product-card{position:absolute;top:134px;width:342px;height:449px;background:var(--white)}
.product-photo{position:absolute;left:10px;top:11px;width:322px;height:204px}
.product-title{position:absolute;left:10px;top:231px;font-size:22px;font-weight:700;color:var(--orange)}
.product-text{position:absolute;left:10px;top:266px;width:292px;font-size:13.5px;line-height:26px;color:var(--text)}
.product-actions{position:absolute;left:10px;top:384px;display:flex;gap:9px}
.product-actions .btn{height:37px;line-height:37px}
.btn-buy{background:var(--slate);width:117px}
.btn-info{background:var(--amber);width:118px}

/* how it works */
.how{position:absolute;left:0;top:1575px;width:1200px;height:456px}
.how .heading{position:absolute;top:55px}
.step{position:absolute;top:177px;width:220px;text-align:center}
.step-circle{width:149px;height:149px;border-radius:50%;margin:0 auto;display:flex;align-items:center;justify-content:center}
.step-label{margin-top:28px;font-size:22px;line-height:29px;color:var(--text)}
.step-raised .step-label{margin-top:17px}
.c-orange{background:var(--orange)}
.c-amber{background:var(--amber)}
.flow-arrow{position:absolute}

/* decor */
.decor{position:absolute;left:0;top:2031px;width:1200px;height:391px;background:var(--cream-band)}
.decor .heading{position:absolute;top:52px}
.decor-tile{position:absolute;top:152px;width:254px;height:189px}
.decor-tile::after{content:"";position:absolute;inset:9px;border:1px solid rgba(255,255,255,.75)}
.decor-label{position:absolute;inset:0;display:flex;align-items:center;justify-content:center;text-align:center;
  font-family:"Lato",sans-serif;font-weight:700;font-size:23px;line-height:32px;color:var(--white);z-index:1}

/* footer */
.site-footer{position:absolute;left:0;top:2422px;width:1200px;height:285px;background:var(--footer)}
.footer-title{position:absolute;top:36px;font-size:15px;color:var(--ink)}
.quick-links{position:absolute;left:81px;top:70px;list-style:none}
.quick-links li{font-size:12px;color:var(--text);height:33px;padding-left:18px;position:relative}
.quick-links li::before{content:"";position:absolute;left:2px;top:5px;width:6px;height:6px;border:1px solid var(--text);border-radius:50%}
.contact-list{position:absolute;left:303px;top:72px}
.contact-row{display:flex;gap:14px;font-size:13px;line-height:17px;color:var(--text);margin-bottom:16px}
.contact-row svg{flex:none}
.field{position:absolute;left:651px;width:238px;background:var(--white);border:1px solid #8a8a8a;font-size:12px;color:var(--text);padding:6px 10px}
.submit{position:absolute;left:651px;top:226px;width:238px;height:33px;line-height:33px}
.social{position:absolute;left:1002px;top:70px}
.social-row{display:flex;align-items:center;gap:14px;height:39px;font-size:13px;color:var(--link-blue)}
.social-dot{width:33px;height:33px;border-radius:50%}
.bottom-bar{position:absolute;left:0;top:2707px;width:1200px;height:50px;background:var(--bar);color:#dddddd;font-size:14px}
.bottom-bar .copy{position:absolute;left:81px;top:16px}
.bottom-bar .accept{position:absolute;right:82px;top:13px;display:flex;align-items:center;gap:6px}
.card-chip{width:28px;height:18px;background:#e8e8e8;border-radius:2px}
</style>
</head>
<body>

<header class="site-header">
  <div class="brand">
    <span class="brand-mark"></span>
    <span class="brand-name">Hire a Lantern</span>
  </div>
  <div class="account">
    <span><svg width="14" height="14" viewBox="0 0 14 14" fill="none" stroke="#777" stroke-width="1.3"><path d="M6 1h7v12H6"/><path d="M1 7h8M6 4l3 3-3 3"/></svg>log in</span>
    <span><svg width="14" height="14" viewBox="0 0 14 14" fill="none" stroke="#777" stroke-width="1.3"><rect x="1" y="1" width="12" height="12"/><path d="M4 5h6M4 8h6"/></svg>Register</span>
  </div>
  <nav class="main-nav">
    <a class="active" href="#">Home</a>
    <a href="#">About Us</a>
    <a href="#">Our Products</a>
    <a href="#">Contact Us</a>
  </nav>
</header>

<section class="hero" role="img" aria-label="Table centrepiece: a white pillar candle in a glass hurricane surrounded by cream roses and greenery, with wine glasses on a reception table">
  <svg class="hero-arrow" style="left:26px" width="30" height="60" viewBox="0 0 30 60" fill="none" stroke="#ffffff" stroke-width="2"><path d="M26 2L4 30l22 28"/></svg>
  <svg class="hero-arrow" style="right:26px" width="30" height="60" viewBox="0 0 30 60" fill="none" stroke="#ffffff" stroke-width="2"><path d="M4 2l22 28L4 58"/></svg>
  <div class="hero-caption">We Design, Manufacture &amp; Personalise Decorative Candles</div>
</section>

<section class="about">
  <h2 class="heading">About Us</h2>
  <p>We are a family owned and operated company and began making decorative candles for all occasions.&nbsp; All of our candles are individually hand made in our candle studio, situated in Larchmere, outside Glowbury.&nbsp; Our wax is local and of a very high quality, and dripless! Our wax is also made with a high melting point, which means it will not melt or bend in hot temperatures.</p>
  <span class="btn btn-orange read-more">Read More</span>
</section>

<section class="products">
  <h2 class="heading">Our Products</h2>

  <article class="product-card" style="left:79px">
    <div class="product-photo" role="img" aria-label="Large white pillar candle on a garden rail with cream roses" style="background:linear-gradient(160deg,#e9ece4,#bcc3a6 55%,#7d8a5a)"></div>
    <h3 class="product-title">Hire Candles</h3>
    <p class="product-text">Do you love using candles for your events but tired of sorting old used candles or buying expensive candles. Believe it or not you can now rent candles.</p>
    <div class="product-actions"><span class="btn btn-buy">Buy Now</span><span class="btn btn-info">More Info</span></div>
  </article>

  <article class="product-card" style="left:429px">
    <div class="product-photo" role="img" aria-label="White floating candles in stemmed glass bowls" style="background:radial-gradient(circle at 50% 45%,#d8cfc9,#8d7a72 60%,#6a5751)"></div>
    <h3 class="product-title">Personalised Candles</h3>
    <p class="product-text">Do you love using candles for your events but tired of sorting old used candles or buying expensive candles. Believe it or not you can now rent candles.</p>
    <div class="product-actions"><span class="btn btn-buy">Buy Now</span><span class="btn btn-info">More Info</span></div>
  </article>

  <article class="product-card" style="left:779px">
    <div class="product-photo" role="img" aria-label="Green and black pillar candles around a silver candlestick" style="background:linear-gradient(180deg,#e4e6e8,#b9bdb7 60%,#7c8a4c)"></div>
    <h3 class="product-title">Décor Hire</h3>
    <p class="product-text">Do you love using candles for your events but tired of sorting old used candles or buying expensive candles. Believe it or not you can now rent candles.</p>
    <div class="product-actions"><span class="btn btn-buy">Buy Now</span><span class="btn btn-info">More Info</span></div>
  </article>
</section>

<section class="how">
  <h2 class="heading">How It Works</h2>

  <svg class="flow-arrow" style="left:250px;top:140px" width="110" height="40" viewBox="0 0 110 40" fill="none" stroke="#cfcfcf" stroke-width="2"><path d="M2 30C35 5 75 5 104 20"/><path d="M92 10l12 10-14 6"/></svg>
  <svg class="flow-arrow" style="left:548px;top:320px" width="110" height="40" viewBox="0 0 110 40" fill="none" stroke="#cfcfcf" stroke-width="2"><path d="M2 10C35 35 75 35 104 18"/><path d="M90 12l14 6-10 12"/></svg>
  <svg class="flow-arrow" style="left:843px;top:140px" width="110" height="40" viewBox="0 0 110 40" fill="none" stroke="#cfcfcf" stroke-width="2"><path d="M2 30C35 5 75 5 104 20"/><path d="M92 10l12 10-14 6"/></svg>

  <div class="step" style="left:44px">
    <div class="step-circle c-orange">
      <svg width="60" height="80" viewBox="0 0 60 80" fill="#ffffff"><path d="M30 2c6 8 8 13 0 20-8-7-6-12 0-20z"/><rect x="14" y="28" width="32" height="14" rx="2"/><rect x="14" y="45" width="32" height="14" rx="2"/><rect x="14" y="62" width="32" height="14" rx="2"/></svg>
    </div>
    <div class="step-label">Choose your<br>Candle</div>
  </div>

  <div class="step" style="left:340px">
    <div class="step-circle c-amber">
      <svg width="64" height="80" viewBox="0 0 64 80" fill="#ffffff"><rect x="18" y="4" width="12" height="44" rx="6"/><path d="M16 40h34a8 8 0 0 1 8 8v14c0 10-8 16-18 16H30c-10 0-16-8-18-16l-4-14c-1-4 4-7 8-4z"/></svg>
    </div>
    <div class="step-label">Book your<br>Candle</div>
  </div>

  <div class="step" style="left:640px">
    <div class="step-circle c-orange">
      <svg width="80" height="60" viewBox="0 0 80 60" fill="none" stroke="#ffffff" stroke-width="4"><rect x="4" y="14" width="72" height="40" rx="3"/><circle cx="40" cy="34" r="9"/><path d="M10 10l50-8"/></svg>
    </div>
    <div class="step-label">Make<br>payment</div>
  </div>

  <div class="step step-raised" style="left:934px">
    <div class="step-circle c-amber">
      <svg width="70" height="80" viewBox="0 0 70 80" fill="none" stroke="#ffffff" stroke-width="3.5"><path d="M35 2c5 7 6 11 0 16-6-5-5-9 0-16z" fill="#ffffff"/><rect x="25" y="24" width="20" height="38"/><path d="M6 64h58c-2 8-10 12-29 12S8 72 6 64z"/></svg>
    </div>
    <div class="step-label">Light Up<br>Your Event</div>
  </div>
</section>

<section class="decor">
  <h2 class="heading">Our Hiring Out Decor</h2>
  <div class="decor-tile" style="left:81px;background:linear-gradient(150deg,#4a3a2c,#8a7656 55%,#2d241c)" role="img" aria-label="White pillar candles in tall glass vases"><span class="decor-label">Glass Vases</span></div>
  <div class="decor-tile" style="left:343px;background:linear-gradient(150deg,#6e5e42,#a79a78 55%,#5a4b33)" role="img" aria-label="Glass candelabras with lit candles"><span class="decor-label">Candle Bras</span></div>
  <div class="decor-tile" style="left:605px;background:linear-gradient(150deg,#3c3c3c,#8d8a86 55%,#2b2b2b)" role="img" aria-label="Lace chair sash tied on a covered chair"><span class="decor-label">Overlays &amp;<br>Chairs Sachets</span></div>
  <div class="decor-tile" style="left:867px;background:linear-gradient(150deg,#3a3034,#a58d92 55%,#4a3a3e)" role="img" aria-label="Row of white chair covers with pink bows"><span class="decor-label">Chair Covers</span></div>
</section>

<footer class="site-footer">
  <div class="footer-title" style="left:81px">Quick Links</div>
  <ul class="quick-links">
    <li>Home</li><li>About Us</li><li>Our Products</li><li>Contact Us</li>
  </ul>

  <div class="footer-title" style="left:303px">Contact Details</div>
  <div class="contact-list">
    <div class="contact-row"><svg width="18" height="20" viewBox="0 0 18 20" fill="none" stroke="#777" stroke-width="1.5"><path d="M9 19s7-7 7-11A7 7 0 0 0 2 8c0 4 7 11 7 11z"/><circle cx="9" cy="8" r="2.5"/></svg><span>14 Wickfield Lane, Glowbury<br>Harbour - 40218</span></div>
    <div class="contact-row" style="margin-top:6px"><svg width="18" height="20" viewBox="0 0 18 20" fill="none" stroke="#777" stroke-width="1.5"><path d="M4 2h3l2 5-2 2c1 2 3 4 5 5l2-2 4 2v3c0 1-1 2-2 2C9 19 1 11 1 4c0-1 1-2 3-2z"/></svg><span style="font-size:15px">123-555-0148</span></div>
    <div class="contact-row" style="margin-top:10px"><svg width="18" height="14" viewBox="0 0 18 14" fill="none" stroke="#777" stroke-width="1.5"><rect x="1" y="1" width="16" height="12"/><path d="M1 1l8 7 8-7"/></svg><span>hello@hirealantern.com</span></div>
  </div>

  <div class="footer-title" style="left:651px">Quick Inquiry</div>
  <div class="field" style="top:70px;height:33px">Name</div>
  <div class="field" style="top:109px;height:33px">Phone</div>
  <div class="field" style="top:147px;height:74px">Message</div>
  <span class="btn btn-orange submit">Submit</span>

  <div class="footer-title" style="left:1002px">Follow Us</div>
  <div class="social">
    <div class="social-row"><span class="social-dot" style="background:#3b5a9a"></span>Friendwall</div>
    <div class="social-row"><span class="social-dot" style="background:#39a9e0"></span>Chirpline</div>
    <div class="social-row"><span class="social-dot" style="background:#1d7ab8"></span>WorkLink</div>
    <div class="social-row" style="color:#d1422f"><span class="social-dot" style="background:#d1422f"></span>Circle Plus</div>
  </div>
</footer>

<div class="bottom-bar">
  <span class="copy">Copyright © 2016 Hire a Lantern. All Rights Reserved.</span>
  <span class="accept">We Accept:&nbsp; <span class="card-chip"></span><span class="card-chip"></span><span class="card-chip"></span><span class="card-chip"></span></span>
</div>

</body>
</html>
```